Business Card Design

We need a design for business cards for our company. We have a logo. We teach EMT's and we are based out of Virginia. The information that will need to add would be, name, title, phone number, email, address. On the back of the business card would be "Trained today, ready always"

Target Market(s)

People that want to become EMT's

Colors

Designer to choose colors to be used in the design.

Requirements
Must have
• company logo

```html
<!DOCTYPE html>
<html lang="en">
<head>
<meta charset="UTF-8">
<title>Crestline Rescue Academy – Business Cards</title>
<link rel="stylesheet" href="https://fonts.googleapis.com/css2?family=Montserrat:wght@400;500;700;800&display=swap">
<style>
  :root {
    --backdrop: #2b2e33;
    --card-white: #ffffff;
    --card-navy: #1f2a33;
    --brand-red: #c41e2e;
    --text-gray: #4a4f55;
    --rule-gray: #9a9ea3;
  }
  * { margin: 0; padding: 0; box-sizing: border-box; }
  html, body {
    width: 1200px; height: 900px; overflow: hidden;
    background: var(--backdrop);
    font-family: "Montserrat", sans-serif;
  }
  .canvas {
    position: relative; width: 1200px; height: 900px;
    display: flex; align-items: center; justify-content: center; gap: 60px;
  }
  .card {
    position: relative; width: 510px; height: 291px;
    border-radius: 3px; overflow: hidden;
    box-shadow: 0 12px 30px rgba(0,0,0,0.35);
  }
  .card-front { background: var(--card-white); }
  .card-back { background: var(--card-navy); }

  .brand {
    display: flex; align-items: center; gap: 10px;
    color: var(--brand-red); font-weight: 700;
    text-transform: uppercase; letter-spacing: 0.02em;
    white-space: nowrap;
  }
  .brand-dot { flex: none; border-radius: 50%; background: var(--brand-red); }
  .brand-name { line-height: 1.1; }

  .front-brand { position: absolute; top: 46px; right: 44px; font-size: 22px; }
  .front-brand .brand-dot { width: 16px; height: 16px; }

  .holder { position: absolute; top: 120px; right: 44px; text-align: right; }
  .holder-name {
    color: var(--brand-red); font-weight: 800; font-size: 20px;
    text-transform: uppercase; letter-spacing: 0.03em;
  }
  .holder-title { color: var(--text-gray); font-weight: 500; font-size: 14px; margin-top: 2px; }

  .divider {
    position: absolute; left: 0; right: 80px; top: 186px;
    height: 1px; background: var(--rule-gray);
  }

  .contacts { position: absolute; top: 204px; right: 24px; list-style: none; text-align: right; }
  .contact {
    display: flex; align-items: center; justify-content: flex-end; gap: 8px;
    color: var(--text-gray); font-size: 15px; font-weight: 500; line-height: 1.6;
  }
  .contact svg { width: 14px; height: 14px; flex: none; }

  .back-brand {
    position: absolute; top: 92px; left: 0; right: 0;
    justify-content: center; font-size: 26px;
  }
  .back-brand .brand-dot { width: 18px; height: 18px; }

  .tagline-band {
    position: absolute; left: 0; right: 0; bottom: 0; height: 56px;
    background: var(--brand-red);
    display: flex; align-items: center; padding-left: 62px;
  }
  .tagline {
    color: #fff; font-weight: 700; font-size: 13px;
    letter-spacing: 0.2em; text-transform: uppercase; white-space: nowrap;
  }
</style>
</head>
<body>
  <main class="canvas">
    <section class="card card-front" aria-label="Business card front">
      <div class="brand front-brand">
        <span class="brand-dot"></span>
        <span class="brand-name">Crestline Rescue Academy</span>
      </div>
      <div class="holder">
        <div class="holder-name">Daniel Harper</div>
        <div class="holder-title">Sales Manager</div>
      </div>
      <div class="divider"></div>
      <ul class="contacts">
        <li class="contact">555-210-4832
          <svg viewBox="0 0 16 16" aria-hidden="true"><circle cx="8" cy="8" r="7" fill="none" stroke="#c41e2e" stroke-width="1.3"/><path d="M5.5 4.5l1.5 1.5-1 1c.6 1.2 1.4 2 2.6 2.6l1-1 1.5 1.5-1 1.2C7.8 11 5 8.2 4.4 5.7z" fill="#c41e2e"/></svg>
        </li>
        <li class="contact">info@crestlinerescue.com
          <svg viewBox="0 0 16 16" aria-hidden="true"><rect x="1.5" y="3.5" width="13" height="9" fill="none" stroke="#c41e2e" stroke-width="1.3"/><path d="M1.5 3.5L8 9l6.5-5.5" fill="none" stroke="#c41e2e" stroke-width="1.3"/></svg>
        </li>
      </ul>
    </section>

    <section class="card card-back" aria-label="Business card back">
      <div class="brand back-brand">
        <span class="brand-dot"></span>
        <span class="brand-name">Crestline Rescue Academy</span>
      </div>
      <div class="tagline-band">
        <p class="tagline">Trained today, ready always</p>
      </div>
    </section>
  </main>
</body>
</html>
```